TuneRoost - Music Industry App needs a top quality wordpress homepage

We need a modern responsive wordpress homepage built. Our website will only feature one page with the goal to get people to sign up to our app. A word document has been uploaded outlining the page content/sections.

Once the homepage is finalised, I will also need 2 landing pages built as part of this competition. It will be very similar to the homepage with the same layout etc but just feature different images and content. The homepage is for anyone (artists and venues) to find out about us but the landing pages will be artist or venue specific.

The completed work must be delivered as an exportable file into wordpress and be designed properly so no more work is needed to begin utilising as the actual website. The images used must be setup correctly for speed and quality also.

Target Market(s)

Venues and Artists.

Coding

Coded - Design and coding required

Requirements
Must have
• UPDATE: High Res Logo files attached
• Must be a modern looking website and be responsive. Must look good across all devices from desktop, to mobile and tablet. Needs to be very high quality.
• Please see the attached logo - I am waiting for the final high quality version and will reupload when complete but this will be enough to get you started for now. The website must have a dark base colour and have red/white elements to match the logo. The red colour used MUST match the red colour used in the logo.
• Please have a go at creating it how you think is best and provide feedback from there. I am leaving it very open to the designers so I can get the best website possible and lots of different ideas etc.

```html
<!DOCTYPE html>
<html lang="en">
<head>
<meta charset="utf-8">
<title>TuneRoost – Live Music Booking</title>
<link rel="stylesheet" href="https://fonts.googleapis.com/css2?family=Montserrat:wght@400;500&family=Open+Sans:wght@400;600&display=swap">
<style>
:root{
  --red:#e3000f;
  --red-dark:#6e0a12;
  --black:#000;
  --ink:#111;
  --light:#f3f1f2;
  --card:#fff;
  --grey-text:#444;
  --muted:#cfcfcf;
  --panel:#2d2d2d;
  --circle:#2b2b2b;
  --icon-bg:#e3e3e3;
}
*{margin:0;padding:0;box-sizing:border-box}
html,body{width:1200px;height:3362px;overflow:hidden;background:var(--black)}
body{position:relative;font-family:"Open Sans",Arial,sans-serif;color:#fff}
.display{font-family:"Montserrat",Arial,sans-serif;font-weight:400}
.abs{position:absolute}
.center{left:0;width:1200px;text-align:center}

/* hero */
.hero{top:0;left:0;width:1200px;height:760px;
  background:radial-gradient(ellipse at 50% 25%,#b3121f 0%,#8a0d18 35%,#5a0810 65%,#1a0204 88%,#000 100%)}
.brand{top:40px;left:0;width:1200px;display:flex;justify-content:center;align-items:center;gap:14px}
.brand-dot{width:34px;height:34px;border-radius:50%;background:var(--red)}
.brand-name{font-family:"Montserrat",sans-serif;font-weight:400;font-size:46px;color:#fff}
.hero-title{top:258px;font-size:50px}
.hero-sub{top:330px;font-size:31px;line-height:35px}
.hero-join{top:433px;font-size:23px}
.signup{display:flex;align-items:center;background:#fff;padding:6px 8px 6px 22px}
.signup span{flex:1;color:#555;font-size:15px;font-family:"Montserrat",sans-serif}
.signup b{background:var(--red);color:#fff;font-weight:400;font-family:"Montserrat",sans-serif;font-size:18px;height:100%;display:flex;align-items:center;justify-content:center}
.hero-form{top:480px;left:353px;width:500px;height:53px}
.hero-form b{width:138px;height:41px}

/* steps */
.steps-title{top:796px;font-size:30px}
.step{top:887px;width:200px;margin-left:-100px;text-align:center}
.step-icon{width:96px;height:96px;border-radius:50%;background:var(--circle);margin:0 auto;display:flex;align-items:center;justify-content:center}
.step-num{font-family:"Montserrat",sans-serif;font-size:34px;margin-top:18px;line-height:40px}
.step-text{font-size:14.5px;line-height:23px;color:#ddd;margin-top:10px;font-family:"Montserrat",sans-serif}

/* why */
.why{top:1250px;left:0;width:1200px;height:520px;background:var(--light)}
.why-title{top:1298px;font-size:33px;color:var(--ink)}
.card{top:1373px;width:225px;height:287px;background:var(--card);text-align:center;color:var(--grey-text)}
.card-icon{width:80px;height:80px;border-radius:50%;background:var(--icon-bg);margin:34px auto 0;display:flex;align-items:center;justify-content:center}
.card-rule{width:24px;height:2px;background:var(--red);margin:34px auto 0}
.card h3{font-size:18px;font-weight:600;color:var(--ink);margin-top:16px}
.card p{font-size:14px;line-height:20px;margin:10px 14px 0}

/* artists */
.artists{top:1750px;left:0;width:1200px;height:540px;
  background:linear-gradient(90deg,#0a0f22 0%,#14204a 40%,#1f2f6a 60%,#0d1530 100%)}
.artists-title{top:1840px;left:162px;font-size:28px}
.benefits{top:1893px;left:167px;list-style:none;font-size:16px;line-height:29.4px;color:#eee}
.benefits li{display:flex;align-items:center;gap:8px}
.artists-cta{top:2070px;left:167px;font-size:17px;font-weight:600;font-family:"Montserrat",sans-serif}
.artist-form{top:2107px;left:167px;width:499px;height:54px}
.artist-form b{width:139px;height:42px}

/* about */
.about{top:2285px;left:0;width:1200px;height:471px;
  background:radial-gradient(ellipse at 50% 0%,#3a2a4e 0%,#231a30 40%,#141018 75%,#0b0b0b 100%)}
.about-title{top:2368px;font-size:40px}
.about-text{top:2438px;left:280px;width:640px;text-align:center;font-size:14.5px;line-height:23px;color:#ddd}

/* contact */
.contact{top:2756px;left:0;width:615px;height:505px;background:var(--panel)}
.map{top:2756px;left:615px;width:585px;height:505px;background:linear-gradient(135deg,#e9e9e9,#dcdcdc)}
.contact-title{top:2808px;left:159px;font-size:34px}
.field{left:159px;width:391px;border-bottom:1px solid #bdbdbd;font-size:16px;color:#eee;padding-bottom:6px}
.submit{top:3129px;left:163px;width:153px;height:42px;background:var(--red);font-size:18px;display:flex;align-items:center;justify-content:center;font-family:"Montserrat",sans-serif}

/* footer */
.footer{top:3261px;left:0;width:1200px;height:101px;background:var(--black)}
.footer-text{top:3303px;font-size:15px;font-family:"Montserrat",sans-serif}
</style>
</head>
<body>

<section class="abs hero" role="img" aria-label="Concert crowd with raised hands under red stage light"></section>
<div class="abs brand"><span class="brand-dot"></span><span class="brand-name">TuneRoost</span></div>
<h1 class="abs center display hero-title">RideLoop for Live Music</h1>
<p class="abs center display hero-sub">TuneRoost connects venues with artists to<br>make booking gigs simple</p>
<p class="abs center display hero-join">Join Now for FREE</p>
<div class="abs signup hero-form"><span>Email address</span><b>Join Now</b></div>

<h2 class="abs center display steps-title">How TuneRoost Works</h2>
<div class="abs step" style="left:238px">
  <div class="step-icon"><svg width="44" height="48" viewBox="0 0 44 48" fill="none" stroke="#e3000f" stroke-width="3"><rect x="4" y="4" width="30" height="40" rx="2"/><path d="M10 16h18M10 24h18M10 32h10"/><path d="M38 10l-12 14"/></svg></div>
  <div class="step-num">1</div>
  <p class="step-text">Sign up for free and<br>create an artist profile</p>
</div>
<div class="abs step" style="left:419px">
  <div class="step-icon"><svg width="44" height="44" viewBox="0 0 44 44" fill="#e3000f"><circle cx="12" cy="30" r="6"/><rect x="16" y="8" width="3" height="23"/><path d="M19 8l12 4v5l-12-4z"/><rect x="22" y="34" width="18" height="4"/></svg></div>
  <div class="step-num">2</div>
  <p class="step-text">Get in front of venues<br>looking for artists<br>for their gigs</p>
</div>
<div class="abs step" style="left:598px">
  <div class="step-icon"><svg width="48" height="48" viewBox="0 0 48 48" fill="none" stroke="#e3000f" stroke-width="3"><circle cx="24" cy="23" r="18"/><path d="M15 18h18M15 24h18M15 30h12"/></svg></div>
  <div class="step-num">3</div>
  <p class="step-text">Venues request a quote<br>and communicate<br>with you direct</p>
</div>
<div class="abs step" style="left:784px">
  <div class="step-icon"><svg width="50" height="44" viewBox="0 0 50 44" fill="none" stroke="#e3000f" stroke-width="3"><rect x="3" y="8" width="22" height="12" rx="2"/><circle cx="36" cy="28" r="10"/><path d="M36 22v12M33 25h5M33 31h5"/></svg></div>
  <div class="step-num">4</div>
  <p class="step-text">The gig is booked<br>in once payment is<br>provided by the venue.</p>
</div>
<div class="abs step" style="left:966px">
  <div class="step-icon"><svg width="48" height="48" viewBox="0 0 48 48" fill="none" stroke="#e3000f" stroke-width="3"><circle cx="24" cy="24" r="20"/><path d="M15 24l6 6 12-12"/></svg></div>
  <div class="step-num">5</div>
  <p class="step-text">Upon completion the<br>money is paid to you<br>within 48 hours or less.</p>
</div>

<section class="abs why"></section>
<h2 class="abs center display why-title">Why TuneRoost?</h2>
<div class="abs card" style="left:116px">
  <div class="card-icon"><svg width="44" height="40" viewBox="0 0 44 40" fill="none" stroke="#e3000f" stroke-width="3"><rect x="3" y="3" width="34" height="28" rx="2"/><path d="M14 17l5 5 9-9"/><path d="M30 26l10 10"/></svg></div>
  <div class="card-rule"></div><h3>Simple</h3>
  <p>TuneRoost saves time and makes it easy to get gigs</p>
</div>
<div class="abs card" style="left:360px">
  <div class="card-icon"><svg width="50" height="34" viewBox="0 0 50 34" fill="#e3000f"><path d="M2 4l12 4 10 8 4 8-4 4L8 16 2 14z"/><path d="M48 4l-12 4-12 6 6 4 10-4 8 2z"/></svg></div>
  <div class="card-rule"></div><h3>Connect</h3>
  <p>Become part of the TuneRoost community and promote yourself.</p>
</div>
<div class="abs card" style="left:603px">
  <div class="card-icon"><svg width="40" height="46" viewBox="0 0 40 46"><path d="M20 2l17 6v14c0 11-8 19-17 22C11 41 3 33 3 22V8z" fill="#e3000f"/><path d="M12 22l6 6 11-12" fill="none" stroke="#fff" stroke-width="3.5"/></svg></div>
  <div class="card-rule"></div><h3>Protection</h3>
  <p>We ensure you’re protected by getting payment upfront.</p>
</div>
<div class="abs card" style="left:848px">
  <div class="card-icon"><svg width="44" height="46" viewBox="0 0 44 46"><circle cx="24" cy="13" r="11" fill="#e3000f"/><text x="24" y="18" fill="#fff" font-size="14" font-family="Arial,sans-serif" text-anchor="middle">$</text><path d="M2 34l10-6h12l14-4-2 6-14 10H2z" fill="#e3000f"/></svg></div>
  <div class="card-rule"></div><h3>Price</h3>
  <p>Get top dollar by negotiating your price and not paying high agent fees</p>
</div>

<section class="abs artists" role="img" aria-label="Performer on stage under blue lights with crowd"></section>
<h2 class="abs display artists-title">Artists</h2>
<ul class="abs benefits">
  <li><svg width="10" height="12" viewBox="0 0 10 12"><path d="M2 1l5 5-5 5" fill="none" stroke="#fff" stroke-width="2.5"/></svg>Sign up to TuneRoost for FREE and get yourself in front of venues</li>
  <li><svg width="10" height="12" viewBox="0 0 10 12"><path d="M2 1l5 5-5 5" fill="none" stroke="#fff" stroke-width="2.5"/></svg>Only pay us if you get a gig - we only get 10% of the fee you charge the venue</li>
  <li><svg width="10" height="12" viewBox="0 0 10 12"><path d="M2 1l5 5-5 5" fill="none" stroke="#fff" stroke-width="2.5"/></svg>All genres and artists welcome - as long as you’re experienced and professional</li>
  <li><svg width="10" height="12" viewBox="0 0 10 12"><path d="M2 1l5 5-5 5" fill="none" stroke="#fff" stroke-width="2.5"/></svg>Get paid within 48 hours or less after the gig guaranteed!</li>
  <li><svg width="10" height="12" viewBox="0 0 10 12"><path d="M2 1l5 5-5 5" fill="none" stroke="#fff" stroke-width="2.5"/></svg>Negotiate your price and don’t pay huge agent fees to ensure you earn top dollar</li>
</ul>
<p class="abs artists-cta">Sign up and create your TuneRoost profile now</p>
<div class="abs signup artist-form"><span>Email address</span><b>Pre-Register</b></div>

<section class="abs about" role="img" aria-label="Dim concert hall with crowd silhouettes"></section>
<h2 class="abs center display about-title">About TuneRoost</h2>
<p class="abs about-text">We are creating a world class business which will change the way gigs are booked and become the next household name in the app space alongside RideLoop and StayNest. We are average Aussie’s with a big dream, living in the Misty Ranges and initially focusing on Port Callow and the Australian market. We want to get a small amount of quality artists and venues utilising and loving our service initially to get the formula right before growing the business to become the #1 gig booking platform worldwide. If you are a professional artist or venue based in Port Callow, we would love to have you along for the journey.</p>

<section class="abs contact"></section>
<h2 class="abs display contact-title">Contact Us</h2>
<div class="abs field" style="top:2872px">Name *</div>
<div class="abs field" style="top:2915px">Company</div>
<div class="abs field" style="top:2965px">E-mail *</div>
<div class="abs field" style="top:3011px">Phone Number</div>
<div class="abs field" style="top:3053px;height:55px">Message</div>
<div class="abs submit">Submit</div>
<section class="abs map" role="img" aria-label="Street map of Kestrel Ridge, Misty Ranges, Eastvale with location pin"></section>

<footer class="abs footer"></footer>
<p class="abs center footer-text">© 2019 TuneRoost&nbsp; All right reserved &nbsp;|&nbsp; Privacy Policy</p>

</body>
</html>
```